Business Card Design for company

We want new business cards. We'd like something different-- yet still highly professional. Our tagline is Guiding vision, building results. Stock photos are ok, as long as they are relevant and look upscale.

Target Market(s)

Architecture/Business Management Consulting/Engineering Consulting

Contact Information for Business Card

dark gray background with pops of blue might be good, but you tell me. You're the designers. Rounded corners might be nice, but again, you tell me.

Font styles to use
Serif
Sans Serif

Colors
3276b5
5c5c5c
9d9d9d
fbfbfb

Requirements
Nice to have
• Something different, but still very professional.

```html
<!DOCTYPE html>
<html lang="en">
<head>
<meta charset="utf-8">
<title>Taverly Group – Business Card</title>
<link rel="stylesheet" href="https://fonts.googleapis.com/css2?family=Roboto:wght@400;500&family=Montserrat:wght@500&display=swap">
<style>
  :root {
    --brand-blue: #3276b5;
    --ink-gray: #5c5c5c;
    --mid-gray: #9d9d9d;
    --paper: #fbfbfb;
    --back-slate: #4d5055;
    --stage: #2b2b2b;
    --divider: #b8b8b8;
    --tagline-ink: #d9d9d9;
  }
  * { margin: 0; padding: 0; box-sizing: border-box; }
  html, body { width: 1125px; height: 1200px; overflow: hidden; }
  body {
    background: var(--stage);
    font-family: "Roboto", Arial, sans-serif;
    position: relative;
  }
  .card {
    position: absolute;
    left: 150px;
    width: 826px;
    height: 472px;
    overflow: hidden;
  }
  .card-front { top: 98px; background: var(--paper); }
  .card-back { top: 630px; background: var(--back-slate); }

  .front-wordmark {
    position: absolute;
    left: 0;
    width: 428px;
    top: 172px;
    text-align: center;
    font-family: "Montserrat", Arial, sans-serif;
    font-weight: 500;
    color: var(--brand-blue);
    line-height: 1;
  }
  .front-wordmark .name-main { display: block; font-size: 72px; letter-spacing: 2px; }
  .front-wordmark .name-sub { display: block; font-size: 30px; letter-spacing: 3px; margin-top: 16px; }

  .divider {
    position: absolute;
    left: 427px;
    top: 92px;
    width: 2px;
    height: 288px;
    background: linear-gradient(to bottom, transparent, var(--divider) 12%, var(--divider) 88%, transparent);
  }

  .contact {
    position: absolute;
    left: 464px;
    top: 98px;
    color: var(--ink-gray);
  }
  .contact-name {
    font-weight: 500;
    font-size: 30px;
    color: var(--brand-blue);
    letter-spacing: 0.5px;
    line-height: 1.1;
  }
  .contact-role {
    font-weight: 500;
    font-size: 20px;
    margin-top: 4px;
  }
  .contact-address {
    font-size: 19px;
    line-height: 25px;
    margin-top: 16px;
  }
  .contact-lines { list-style: none; margin-top: 12px; }
  .contact-lines li {
    display: flex;
    align-items: center;
    font-size: 19px;
    height: 26px;
  }
  .contact-lines svg { width: 18px; height: 18px; margin-right: 14px; fill: var(--brand-blue); flex: none; }

  .accent-band { position: absolute; left: 0; bottom: 0; width: 826px; height: 14px; }

  .back-wordmark {
    position: absolute;
    left: 0; right: 0;
    top: 184px;
    text-align: center;
    font-family: "Montserrat", Arial, sans-serif;
    font-weight: 500;
    font-size: 100px;
    letter-spacing: 3px;
    color: var(--brand-blue);
    line-height: 1;
  }
  .tagline {
    position: absolute;
    left: 0; right: 0;
    top: 398px;
    text-align: center;
    font-size: 20px;
    color: var(--tagline-ink);
  }
  .tagline .dot {
    display: inline-block;
    width: 7px; height: 7px;
    border-radius: 50%;
    background: var(--tagline-ink);
    margin: 0 12px;
    vertical-align: middle;
  }
</style>
</head>
<body>
  <section class="card card-front" aria-label="Business card front">
    <div class="front-wordmark">
      <span class="name-main">TAVERLY</span>
      <span class="name-sub">GROUP</span>
    </div>
    <div class="divider"></div>
    <div class="contact">
      <div class="contact-name">DANIEL HART</div>
      <div class="contact-role">CEO/FOUNDER</div>
      <div class="contact-address">2140 Cedar Ridge Road<br>Portland, Oregon 97205</div>
      <ul class="contact-lines">
        <li><svg viewBox="0 0 24 24" aria-hidden="true"><path d="M6.6 10.8a15.1 15.1 0 0 0 6.6 6.6l2.2-2.2a1 1 0 0 1 1-.25 11.4 11.4 0 0 0 3.6.57 1 1 0 0 1 1 1V20a1 1 0 0 1-1 1A17 17 0 0 1 3 4a1 1 0 0 1 1-1h3.5a1 1 0 0 1 1 1c0 1.25.2 2.45.57 3.57a1 1 0 0 1-.25 1z"/></svg>503 218 4471</li>
        <li><svg viewBox="0 0 24 24" aria-hidden="true"><path d="M7 1h10a2 2 0 0 1 2 2v18a2 2 0 0 1-2 2H7a2 2 0 0 1-2-2V3a2 2 0 0 1 2-2zm0 3v15h10V4zm5 16.2a1 1 0 1 0 0 .01z"/></svg>503 662 9085</li>
        <li><svg viewBox="0 0 24 24" aria-hidden="true"><path d="M7 2h10v5H7zM4 8h16a2 2 0 0 1 2 2v8h-3v4H5v-4H2v-8a2 2 0 0 1 2-2zm3 8v4h10v-4z"/></svg>503 218 4472</li>
        <li><svg viewBox="0 0 24 24" aria-hidden="true"><path d="M2 5h20v14H2zm2 2v.5l8 5 8-5V7zm0 2.8V17h16V9.8l-8 5z"/></svg>daniel@taverlygroup.com</li>
        <li><svg viewBox="0 0 24 24" aria-hidden="true"><path d="M12 2a10 10 0 1 0 0 20 10 10 0 0 0 0-20zm-1 17.9A8 8 0 0 1 4.2 10.2L9 15v1a2 2 0 0 0 2 2zm6.9-2.5A2 2 0 0 0 16 16h-1v-3a1 1 0 0 0-1-1H8v-2h2a1 1 0 0 0 1-1V7h2a2 2 0 0 0 2-2v-.4a8 8 0 0 1 2.9 12.8z"/></svg>www.taverlygroup.com</li>
      </ul>
    </div>
    <svg class="accent-band" viewBox="0 0 826 14" preserveAspectRatio="none" aria-hidden="true">
      <polygon points="0,2 540,2 536,14 0,14" fill="var(--brand-blue)"/>
      <polygon points="545,0 826,0 826,14 540,14" fill="var(--ink-gray)"/>
    </svg>
  </section>

  <section class="card card-back" aria-label="Business card back">
    <div class="back-wordmark">TAVERLY</div>
    <p class="tagline">Guiding vision<span class="dot"></span>building results</p>
  </section>
</body>
</html>
```